Specialised investor in e-mobility and energy wants business card design

We need a business card design that fits our existing corporate design. <The look and feel must be 'sharp'/'clean', dynamic, communicate momentum, professionalism etc (as one would imagine from a firm in the financial sector). We like the idea of a reverse-side of the card that includes the logo, and the name and contact details on the other. We expect the deliverable to be whatever format might be required to be able to get cards printed directly by a service such as kelmo press. Our website is www.zub.capital

```html
<!DOCTYPE html>
<html lang="en">
<head>
<meta charset="utf-8">
<title>ZUB Capital – Business Card</title>
<link rel="stylesheet" href="https://fonts.googleapis.com/css2?family=Lato:wght@400;700&display=swap">
<style>
  :root {
    --bg: #1e1e1e;
    --card: #ffffff;
    --green-dark: #324f26;
    --green-light: #7fb547;
    --ink-light: #ffffff;
  }
  * { box-sizing: border-box; margin: 0; padding: 0; }
  html, body { width: 1200px; height: 1122px; overflow: hidden; }
  body {
    background: var(--bg);
    font-family: "Lato", sans-serif;
    position: relative;
  }
  .card {
    position: absolute;
    left: 180px;
    width: 840px;
    height: 480px;
    background: var(--card);
    border-radius: 28px;
    overflow: hidden;
  }
  .card--front { top: 54px; }
  .card--back { top: 588px; }

  .brand {
    position: absolute;
    display: flex;
    align-items: center;
    gap: 18px;
    color: var(--green-dark);
    font-weight: 400;
    font-size: 74px;
    letter-spacing: 1px;
    white-space: nowrap;
  }
  .brand__dot {
    width: 22px; height: 22px;
    border-radius: 50%;
    background: var(--green-light);
  }
  .card--front .brand { left: 50%; top: 50%; transform: translate(-50%, -56%); }
  .card--back .brand { left: 50%; top: 58px; transform: translateX(-45%); }

  .band {
    position: absolute;
    left: 0; right: 0; bottom: 0;
    height: 250px;
    background: var(--green-dark);
  }
  .person {
    position: absolute;
    right: 470px;
    top: 78px;
    text-align: right;
  }
  .person__name {
    color: var(--green-light);
    font-weight: 700;
    font-size: 36px;
    letter-spacing: 0.5px;
  }
  .person__role {
    color: var(--ink-light);
    font-size: 22px;
    margin-top: 2px;
  }
  .divider {
    position: absolute;
    left: 410px;
    top: 58px;
    width: 1px;
    height: 132px;
    background: rgba(255,255,255,0.55);
  }
  .contact {
    position: absolute;
    left: 450px;
    top: 66px;
    list-style: none;
  }
  .contact__item {
    display: flex;
    align-items: center;
    gap: 14px;
    color: var(--ink-light);
    font-size: 21px;
    line-height: 40px;
  }
  .contact__icon { width: 18px; height: 18px; flex: none; }
</style>
</head>
<body>
  <section class="card card--front" aria-label="Card front">
    <div class="brand"><span class="brand__dot"></span><span>ZUB Capital</span></div>
  </section>

  <section class="card card--back" aria-label="Card back">
    <div class="brand"><span class="brand__dot"></span><span>ZUB Capital</span></div>
    <div class="band">
      <div class="person">
        <div class="person__name">MARK ELSTOW</div>
        <div class="person__role">Founder &amp; CEO</div>
      </div>
      <div class="divider"></div>
      <ul class="contact">
        <li class="contact__item">
          <svg class="contact__icon" viewBox="0 0 24 24" aria-hidden="true"><path fill="#7fb547" d="M6.6 10.8a15.1 15.1 0 0 0 6.6 6.6l2.2-2.2a1 1 0 0 1 1-.25 11.4 11.4 0 0 0 3.6.57 1 1 0 0 1 1 1V20a1 1 0 0 1-1 1A17 17 0 0 1 3 4a1 1 0 0 1 1-1h3.5a1 1 0 0 1 1 1c0 1.25.2 2.45.57 3.57a1 1 0 0 1-.25 1z"/></svg>
          <span>+41 79555 0142</span>
        </li>
        <li class="contact__item">
          <svg class="contact__icon" viewBox="0 0 24 24" aria-hidden="true"><path fill="#7fb547" d="M2 5h20v14H2z"/><path fill="none" stroke="#324f26" stroke-width="2" d="M2 5l10 8 10-8"/></svg>
          <span>mark@zub.capital</span>
        </li>
        <li class="contact__item">
          <svg class="contact__icon" viewBox="0 0 24 24" aria-hidden="true"><circle cx="12" cy="12" r="10" fill="#7fb547"/><path fill="none" stroke="#324f26" stroke-width="1.5" d="M2 12h20M12 2c3 3 3 17 0 20M12 2c-3 3-3 17 0 20"/></svg>
          <span>www.zub.capital</span>
        </li>
      </ul>
    </div>
  </section>
</body>
</html>
```